Billboard Velto-Link Systems

Design of an A0 billboard (landscape, will be printed on adhesive foil) of our company with reference to the website (www.velto-link.example) and the activity through keywords / phrases such as Fastest data radio you can buy, data radio safe and independent , ...
Explanation: we set up radio networks for long-range data transmission, which work on our own frequencies and are therefore independent of the provider. The systems are used for water and energy supply systems, sewage systems, environmental measurement networks, ...

Industry/Entity Type

Water-, Energie- Distribution, Abwasser...

Requirements
Must have
• Logo, link on website
Nice to have
• Message
Should not have
• picture of our old product from present web. I will be discontinued shortly. Please use the new one I uploaded here.

```html
<!DOCTYPE html>
<html lang="en">
<head>
<meta charset="utf-8">
<title>Velto-Link Systems – Billboard</title>
<link rel="stylesheet" href="https://fonts.googleapis.com/css2?family=Figtree:wght@500&family=Encode+Sans+Condensed:wght@400&display=swap">
<style>
  :root {
    --brand-blue: #3c6496;
    --sky-light: #eef0f7;
    --sky-mid: #d6dae9;
    --ink: #111111;
    --paper: #ffffff;
  }
  html, body {
    margin: 0;
    padding: 0;
    overflow: hidden;
    background: var(--paper);
  }
  .billboard {
    position: relative;
    width: 1200px;
    height: 848px;
    overflow: hidden;
    background: var(--paper);
  }
  .billboard__shapes {
    position: absolute;
    inset: 0;
  }
  .brand-name {
    position: absolute;
    left: 70px;
    top: 58px;
    margin: 0;
    font-family: "Figtree", sans-serif;
    font-weight: 500;
    font-size: 38px;
    letter-spacing: 0.5px;
    color: var(--paper);
  }
  .headline {
    position: absolute;
    left: 70px;
    top: 270px;
    margin: 0;
    font-family: "Figtree", sans-serif;
    font-weight: 500;
    font-size: 104px;
    line-height: 124px;
    letter-spacing: 0.5px;
    color: var(--brand-blue);
  }
  .headline span { display: block; }
  .web-address {
    position: absolute;
    left: 70px;
    top: 695px;
    width: 533px;
    height: 84px;
    box-sizing: border-box;
    border: 2px solid var(--ink);
    border-radius: 22px;
    display: flex;
    align-items: center;
    justify-content: center;
    font-family: "Encode Sans Condensed", sans-serif;
    font-weight: 400;
    font-size: 46px;
    color: var(--ink);
  }
</style>
</head>
<body>
  <main class="billboard">
    <svg class="billboard__shapes" width="1200" height="848" viewBox="0 0 1200 848" aria-hidden="false">
      <defs>
        <linearGradient id="sky" x1="0" y1="0" x2="1" y2="1">
          <stop offset="0" stop-color="#f6f7fb"/>
          <stop offset="0.5" stop-color="#e4e7f1"/>
          <stop offset="1" stop-color="#cfd4e6"/>
        </linearGradient>
      </defs>
      <path class="pylon-photo" role="img" aria-label="Photograph of high-voltage electricity pylons and power lines against a pale sky"
            d="M494 97 Q900 300 1200 779 L1200 0 L494 0 Z" fill="url(#sky)"/>
      <path class="brand-band" d="M0 0 L1200 0 Q500 40 0 267 Z" fill="var(--brand-blue)"/>
    </svg>

    <p class="brand-name">Velto-Link Systems</p>

    <h1 class="headline">
      <span>Data Radio;</span>
      <span>Safe &amp;</span>
      <span>Independent</span>
    </h1>

    <div class="web-address">www.velto-link.example</div>
  </main>
</body>
</html>
```